BOLD & MINIMALIST DESIGN NEEDED

We want a very bold but minimalistic business card design that is impactful and utilizes both sides of the business card. Our current logo is included for your use.

We want bold fonts and good use of negative space. We don't want the logo to overpower the design.

Target Market(s)

Professionals who are building new commercial buildings.

Industry/Entity Type

Construction

Contact Information for Business Card

Name, Title, email, office phone, cell phone, website

Font styles to use
Serif
Sans Serif

Requirements
Must have
• Bold design!

```html
<!DOCTYPE html>
<html lang="en">
<head>
<meta charset="utf-8">
<title>Ridgecrest Build – Business Card</title>
<link href="https://fonts.googleapis.com/css2?family=Arimo:wght@400;700&display=swap" rel="stylesheet">
<style>
  :root {
    --backdrop: #1b1b1b;
    --card-light: #f4f4f4;
    --card-dark: #1f1f1f;
    --brand-green: #7dbd3d;
    --ink-dark: #1e1e1e;
    --ink-light: #ffffff;
  }
  html, body {
    margin: 0;
    padding: 0;
    width: 1200px;
    height: 1059px;
    overflow: hidden;
    background: var(--backdrop);
    font-family: "Arimo", Arial, sans-serif;
  }
  .canvas { position: relative; width: 1200px; height: 1059px; }

  .card {
    position: absolute;
    border-radius: 18px;
    overflow: hidden;
  }
  .card-front { left: 257px; top: 89px; width: 687px; height: 390px; background: var(--card-light); }
  .card-back  { left: 253px; top: 546px; width: 694px; height: 394px; background: var(--brand-green); }

  .front-band { position: absolute; left: 0; top: 0; width: 687px; height: 390px; }

  .brand {
    position: absolute;
    left: 0; right: 0;
    display: flex;
    align-items: center;
    justify-content: center;
    gap: 12px;
    font-weight: 700;
    letter-spacing: 1px;
  }
  .brand-mark { display: block; }
  .brand-front { top: 88px; font-size: 40px; color: var(--ink-dark); }
  .brand-front .brand-mark { width: 26px; height: 26px; background: var(--brand-green); }
  .brand-back { top: 165px; font-size: 58px; color: var(--ink-light); }
  .brand-back .brand-mark { width: 36px; height: 36px; background: var(--ink-light); }

  .person {
    position: absolute;
    right: calc(687px - 315px);
    top: 270px;
    text-align: right;
  }
  .person-name { margin: 0; font-size: 26px; font-weight: 700; color: var(--brand-green); line-height: 1.1; }
  .person-title { margin: 4px 0 0; font-size: 18px; font-weight: 400; color: var(--ink-light); }

  .divider {
    position: absolute;
    left: 343px; top: 251px;
    width: 1px; height: 95px;
    background: var(--brand-green);
  }

  .contacts {
    position: absolute;
    left: 367px; top: 246px;
    margin: 0; padding: 0;
    list-style: none;
  }
  .contacts li {
    display: flex;
    align-items: center;
    gap: 6px;
    height: 26.5px;
    font-size: 18px;
    color: var(--ink-light);
  }
  .contacts svg { width: 12px; height: 12px; flex: none; }
</style>
</head>
<body>
<div class="canvas">

  <section class="card card-front" aria-label="Business card front">
    <svg class="front-band" viewBox="0 0 687 390" aria-hidden="true">
      <defs>
        <linearGradient id="accentFade" x1="0" x2="1" y1="0" y2="0">
          <stop offset="0" stop-color="#7dbd3d" stop-opacity="0"/>
          <stop offset="0.4" stop-color="#7dbd3d" stop-opacity="0.6"/>
          <stop offset="1" stop-color="#7dbd3d"/>
        </linearGradient>
      </defs>
      <path d="M15 240 Q343 170 670 240 Q343 186 15 240 Z" fill="url(#accentFade)"/>
      <path d="M0 247 Q343 180 687 247 L687 390 L0 390 Z" fill="#1f1f1f"/>
    </svg>

    <div class="brand brand-front">
      <span class="brand-mark"></span>
      <span class="brand-name">RIDGECREST BUILD</span>
    </div>

    <div class="person">
      <p class="person-name">DANIEL MOORE</p>
      <p class="person-title">Owner/CEO</p>
    </div>

    <div class="divider"></div>

    <ul class="contacts">
      <li>
        <svg viewBox="0 0 12 12"><path d="M2.5 1 L4.5 1 L5.2 3.5 L4 4.5 Q5 7 7.5 8 L8.5 6.8 L11 7.5 L11 9.5 Q10.5 11 9 11 Q2 10 1 3 Q1 1.5 2.5 1 Z" fill="#7dbd3d"/></svg>
        <span>07 5120 4400</span>
      </li>
      <li>
        <svg viewBox="0 0 12 12"><rect x="3" y="0.5" width="6" height="11" rx="1" fill="none" stroke="#7dbd3d" stroke-width="1.2"/><circle cx="6" cy="9.6" r="0.7" fill="#7dbd3d"/></svg>
        <span>0412 555 907</span>
      </li>
      <li>
        <svg viewBox="0 0 12 12"><rect x="0.5" y="2.5" width="11" height="7.5" fill="#7dbd3d"/><path d="M0.5 2.5 L6 7 L11.5 2.5" fill="none" stroke="#1f1f1f" stroke-width="1"/></svg>
        <span>hello@ridgecrestbuild.com</span>
      </li>
      <li>
        <svg viewBox="0 0 12 12"><circle cx="6" cy="6" r="5.2" fill="none" stroke="#7dbd3d" stroke-width="1.2"/><path d="M0.8 6 H11.2 M6 0.8 Q3 6 6 11.2 M6 0.8 Q9 6 6 11.2" fill="none" stroke="#7dbd3d" stroke-width="0.9"/></svg>
        <span>www.ridgecrestbuild.com</span>
      </li>
    </ul>
  </section>

  <section class="card card-back" aria-label="Business card back">
    <div class="brand brand-back">
      <span class="brand-mark"></span>
      <span class="brand-name">RIDGECREST BUILD</span>
    </div>
  </section>

</div>
</body>
</html>
```